Upscale business cards needed for Board of Directors

We need professional business cards created for members of our family business Board of Directors. We would like these relatively simple and straightforward, but also with a unique element to set them apart. Probably stick with neutral and simple colors - white, grey etc. We need space for the traditional elements, including name, title, address, email/phone number. And we will be creating several from this template so it needs to be template that is easy to switch information in and out of.
Business
See description

```html
<!DOCTYPE html>
<html lang="en">
<head>
<meta charset="utf-8">
<title>Harborline Holdings – Business Card</title>
<link rel="stylesheet" href="https://fonts.googleapis.com/css2?family=Open+Sans:wght@400;600;700&display=swap">
<style>
  :root {
    --page-bg: #e9e6e2;
    --card-white: #ffffff;
    --ink-dark: #231f20;
    --accent-gold: #b29b6d;
    --text-light: #ffffff;
  }
  * { margin: 0; padding: 0; box-sizing: border-box; }
  html, body {
    width: 1200px;
    height: 900px;
    overflow: hidden;
    background: var(--page-bg);
    font-family: "Open Sans", Arial, sans-serif;
  }
  .business-card {
    position: absolute;
    left: 150px;
    top: 172px;
    width: 900px;
    height: 556px;
    background: var(--card-white);
    overflow: hidden;
    box-shadow: 0 10px 30px rgba(0,0,0,0.15);
  }
  .card-wave {
    position: absolute;
    inset: 0;
    width: 100%;
    height: 100%;
  }
  .holder {
    position: absolute;
    right: 55px;
    top: 34px;
    text-align: right;
  }
  .holder-name {
    color: var(--accent-gold);
    font-weight: 600;
    font-size: 35px;
    line-height: 1.2;
  }
  .holder-title {
    color: var(--ink-dark);
    font-size: 22px;
    line-height: 1.3;
  }
  .company {
    position: absolute;
    left: 58px;
    top: 268px;
    display: flex;
    align-items: center;
    gap: 14px;
  }
  .company-mark {
    width: 26px;
    height: 26px;
    background: var(--accent-gold);
  }
  .company-name {
    color: var(--ink-dark);
    font-weight: 700;
    font-size: 34px;
    line-height: 1.2;
  }
  .contact-list {
    position: absolute;
    right: 55px;
    top: 326px;
    list-style: none;
    color: var(--text-light);
    font-size: 22px;
    text-align: right;
  }
  .contact-list li {
    display: flex;
    justify-content: flex-end;
    align-items: center;
    gap: 12px;
    height: 33px;
  }
  .contact-icon { width: 17px; height: 17px; fill: var(--text-light); }
  .address {
    position: absolute;
    right: 55px;
    top: 440px;
    color: var(--text-light);
    font-size: 22px;
    line-height: 33px;
    text-align: right;
  }
</style>
</head>
<body>
  <div class="business-card">
    <svg class="card-wave" viewBox="0 0 652 403" preserveAspectRatio="none" aria-hidden="true">
      <path d="M0,248 C90,300 170,330 250,322 C380,306 470,166 560,162 C610,160 640,190 652,206"
            fill="none" stroke="var(--accent-gold)" stroke-width="5"/>
      <path d="M0,264 C100,318 180,340 260,332 C380,316 470,180 560,178 C610,177 640,200 652,216 L652,403 L0,403 Z"
            fill="var(--ink-dark)"/>
    </svg>

    <div class="holder">
      <p class="holder-name">Daniel Whitmore</p>
      <p class="holder-title">Managing Director</p>
    </div>

    <div class="company">
      <span class="company-mark" aria-hidden="true"></span>
      <p class="company-name">Harborline Holdings</p>
    </div>

    <ul class="contact-list">
      <li>044-123 456 789
        <svg class="contact-icon" viewBox="0 0 24 24"><path d="M6.6 10.8a15.1 15.1 0 0 0 6.6 6.6l2.2-2.2a1 1 0 0 1 1-.25 11.4 11.4 0 0 0 3.6.57 1 1 0 0 1 1 1V20a1 1 0 0 1-1 1A17 17 0 0 1 3 4a1 1 0 0 1 1-1h3.5a1 1 0 0 1 1 1c0 1.25.2 2.45.57 3.57a1 1 0 0 1-.25 1z"/></svg>
      </li>
      <li>info@webname.com
        <svg class="contact-icon" viewBox="0 0 24 24"><path d="M2 5h20v14H2z" fill="var(--text-light)"/><path d="M3 6.5 12 13.2 21 6.5" fill="none" stroke="var(--ink-dark)" stroke-width="1.6"/></svg>
      </li>
      <li>www.websitename.com
        <svg class="contact-icon" viewBox="0 0 24 24"><path d="M10 14a4 4 0 0 0 5.7 0l3.5-3.5a4 4 0 0 0-5.7-5.7L12 6.3M14 10a4 4 0 0 0-5.7 0l-3.5 3.5a4 4 0 0 0 5.7 5.7L12 17.7" fill="none" stroke="var(--text-light)" stroke-width="2.2" stroke-linecap="round"/></svg>
      </li>
    </ul>

    <p class="address">12345, Address Goes Here<br>Country Name, 123456</p>
  </div>
</body>
</html>
```